SkyvornQ Business Cards and Stationary Design

Need a design for our business cards and stationary. I want to carry on the theme of the logo. I want the business cards to have a design on the back. I would like the business cards and the stationary to carry the same theme, design scheme, and branding

Target Market(s)

Airlines and Maintenance Facilities

Industry/Entity Type

Aviation

Contact Information for Business Card

Name
Position Title
Address: 4827 Trellis Hollow Road, Fort Pierce, Florida, 34951
Office Number
Mobile Number
Email
Website

Font styles to use
Serif
Sans Serif

Colors

Designer to choose colors to be used in the design.

```html
<!DOCTYPE html>
<html lang="en">
<head>
<meta charset="utf-8">
<title>SkyvornQ Business Card</title>
<link rel="stylesheet" href="https://fonts.googleapis.com/css2?family=Open+Sans:wght@300;400;600;700&display=swap">
<style>
  :root {
    --backdrop: #dcdddf;
    --card-white: #ffffff;
    --navy: #1f3163;
    --navy-deep: #223a70;
    --sky: #2a9ad6;
    --sky-mid: #2a7fbe;
    --back-edge: #22558f;
    --text-dark: #2a2a2a;
    --divider: #c9c9c9;
  }
  * { margin: 0; padding: 0; box-sizing: border-box; }
  html, body { width: 1200px; height: 1103px; overflow: hidden; }
  body {
    background: linear-gradient(135deg, #e8e9ea 0%, var(--backdrop) 60%, #d4d5d7 100%);
    font-family: "Open Sans", Arial, sans-serif;
    position: relative;
  }
  .card {
    position: absolute;
    width: 787px;
    border-radius: 46px;
    overflow: hidden;
  }
  .card-front {
    left: 340px; top: 67px; height: 451px;
    background: var(--card-white);
    border: 1px solid #3a3a3a;
  }
  .card-back {
    left: 84px; top: 575px; height: 449px;
    background: radial-gradient(ellipse at 50% 40%, var(--sky) 0%, var(--sky-mid) 50%, var(--back-edge) 100%);
  }
  .footer-band {
    position: absolute; left: 0; bottom: 0;
    width: 100%; height: 92px;
    background: linear-gradient(90deg, var(--navy-deep) 0%, #2a6fb0 50%, var(--navy-deep) 100%);
  }

  .brand-mark {
    position: absolute; left: 189px; top: 110px;
    width: 102px; height: 102px;
    border: 6px solid var(--navy-deep);
    border-radius: 50%;
  }
  .brand-name {
    position: absolute; left: 0; width: 478px; top: 222px;
    text-align: center;
    font-weight: 700; font-size: 38px; letter-spacing: 6px;
    color: var(--navy);
  }
  .divider {
    position: absolute; left: 447px; top: 94px;
    width: 2px; height: 191px; background: var(--divider);
  }
  .person { position: absolute; left: 468px; top: 84px; }
  .person-name {
    font-weight: 700; font-size: 27px; color: var(--navy); line-height: 36px;
  }
  .person-title {
    font-weight: 300; font-size: 24px; color: var(--text-dark); line-height: 34px; letter-spacing: 0.5px;
  }
  .contact-list { list-style: none; margin-top: 12px; }
  .contact-list li {
    display: flex; align-items: center; gap: 6px;
    font-size: 18px; color: var(--text-dark); height: 28px;
  }
  .contact-list svg { width: 18px; height: 18px; flex: none; }
  .address {
    position: absolute; left: 60px; width: 320px; top: 380px;
    text-align: center; color: #ffffff; font-size: 17px; line-height: 29px;
  }
  .address svg { width: 15px; height: 15px; vertical-align: -2px; margin-right: 4px; }

  .back-mark {
    position: absolute; left: 261px; top: 58px;
    width: 266px; height: 266px;
    border: 10px solid var(--navy-deep);
    border-radius: 50%;
    display: flex; align-items: center; justify-content: center;
  }
  .back-name {
    font-weight: 700; font-size: 34px; letter-spacing: 4px; color: #ffffff;
  }
  .back-web {
    position: absolute; left: 0; width: 787px; top: 352px;
    text-align: center; color: #ffffff; font-size: 24px; letter-spacing: 5px;
  }
</style>
</head>
<body>

<section class="card card-front">
  <div class="footer-band" role="img" aria-label="Decorative wave band in navy and sky blue"></div>

  <div class="brand-mark"></div>
  <div class="brand-name">SKYVORNQ</div>

  <div class="divider"></div>

  <div class="person">
    <div class="person-name">DORIAN KESWICK</div>
    <div class="person-title">PRESIDENT</div>
    <ul class="contact-list">
      <li>
        <svg viewBox="0 0 18 18"><circle cx="9" cy="9" r="8" fill="none" stroke="#1f3163" stroke-width="1.4"/><path d="M6,5 L7.5,5 L8.2,7 L7.3,7.8 C7.8,9 8.9,10.1 10.1,10.6 L10.9,9.7 L12.9,10.4 L12.9,11.9 C9,12.2 5.8,9 6,5 Z" fill="#1f3163"/></svg>
        772-555-0148
      </li>
      <li>
        <svg viewBox="0 0 18 18"><circle cx="9" cy="9" r="8" fill="none" stroke="#1f3163" stroke-width="1.4"/><rect x="6.3" y="4.3" width="5.4" height="9.4" rx="1" fill="none" stroke="#1f3163" stroke-width="1.2"/><circle cx="9" cy="12" r="0.7" fill="#1f3163"/></svg>
        772-555-0148
      </li>
      <li>
        <svg viewBox="0 0 18 18"><circle cx="9" cy="9" r="8" fill="none" stroke="#1f3163" stroke-width="1.4"/><rect x="4.8" y="6" width="8.4" height="6" fill="#1f3163"/><path d="M4.8,6 L9,9.3 L13.2,6" fill="none" stroke="#ffffff" stroke-width="0.9"/></svg>
        info@skyvornq.com
      </li>
      <li>
        <svg viewBox="0 0 18 18"><circle cx="9" cy="9" r="8" fill="none" stroke="#1f3163" stroke-width="1.4"/><ellipse cx="9" cy="9" rx="3.3" ry="8" fill="none" stroke="#1f3163" stroke-width="1.1"/><path d="M1,9 H17 M2.5,5 H15.5 M2.5,13 H15.5" stroke="#1f3163" stroke-width="1.1"/></svg>
        www.skyvornq.com
      </li>
    </ul>
  </div>

  <div class="address">
    <svg viewBox="0 0 16 16"><circle cx="8" cy="8" r="7" fill="none" stroke="#ffffff" stroke-width="1.4"/><path d="M8,3.6 C6.2,3.6 5,4.9 5,6.5 C5,8.6 8,12 8,12 C8,12 11,8.6 11,6.5 C11,4.9 9.8,3.6 8,3.6 Z" fill="#ffffff"/><circle cx="8" cy="6.5" r="1.1" fill="#223a70"/></svg>4827 Trellis Hollow Road,<br>Fort Pierce, Florida, 34951
  </div>
</section>

<section class="card card-back">
  <div class="back-mark"><span class="back-name">SKYVORNQ</span></div>
  <div class="back-web">www.skyvornq.com</div>
</section>

</body>
</html>
```